Redesign Local Plumber Website

redesign of existing plumbing website

Mobile Responsive
Professional
modern
easy enquiry
Map embed

Please see existing site for text and images. Please feel free to suggest improvements and any additional features
callthepipeteam.com.au

attached is logo and the Australian owned badge which we also want featuring

Target Market(s)

Plumbing & Gas Services

Industry/Entity Type

Plumbing

Font styles to use
Sans Serif

Requirements
Must have
• existing logo
Nice to have
• new design
Should not have
• same design

```html
<!DOCTYPE html>
<html lang="en">
<head>
<meta charset="utf-8">
<title>Call The Pipe Team – Plumbing &amp; Gas</title>
<link href="https://fonts.googleapis.com/css2?family=Poppins:wght@500;600;700&family=Roboto:wght@400;500;700&display=swap" rel="stylesheet">
<style>
:root{
  --blue:#1a86d0;
  --blue-dark:#1273b8;
  --navy:#0f1a4f;
  --ink:#1c1c1c;
  --text:#6a6a6a;
  --grey-bg:#f2f2f2;
  --sky-bg:#e7f1f6;
  --footer:#1f1f1f;
  --white:#fff;
  --muted-shape:#c9d3da;
}
*{box-sizing:border-box;margin:0;padding:0}
html,body{width:1200px;height:4619px;overflow:hidden}
body{position:relative;font-family:'Roboto',sans-serif;color:var(--ink);background:var(--white)}
.abs{position:absolute}
h1,h2,h3,.poppins{font-family:'Poppins',sans-serif}
.section-title{position:absolute;left:0;width:1200px;text-align:center;font-family:'Poppins',sans-serif;font-weight:700;font-size:34px;color:var(--ink);letter-spacing:-.5px}
.section-title span{color:var(--blue)}
.btn{position:absolute;display:flex;align-items:center;justify-content:center;gap:8px;border-radius:30px;color:var(--white);font-weight:700;font-size:15px;text-transform:uppercase}
.btn svg{width:13px;height:13px}

/* header */
.header{position:absolute;left:0;top:0;width:1200px;height:117px;background:var(--white)}
.logo{position:absolute;left:111px;top:30px;display:flex;align-items:center;gap:12px}
.logo-dot{width:44px;height:44px;border-radius:50%;background:var(--blue)}
.logo-name{font-family:'Poppins',sans-serif;font-weight:700;font-size:26px;color:var(--blue)}
.stay{position:absolute;left:648px;top:28px;font-size:14px;color:var(--ink)}
.social-top{position:absolute;top:24px;display:flex;gap:8px}
.social-top i{display:block;width:28px;height:28px;border-radius:50%;background:var(--blue)}
.estimate{position:absolute;left:918px;top:16px;display:flex;gap:12px;align-items:center}
.estimate small{display:block;font-size:12px}
.estimate b{font-size:20px;font-weight:700}
.nav{position:absolute;top:80px;left:524px;display:flex;gap:28px;font-size:15px;font-weight:500}
.nav a{color:var(--ink);text-decoration:none;position:relative;padding-bottom:12px}
.nav a.active{color:var(--blue)}
.nav a.active::after{content:"";position:absolute;left:-4px;right:-4px;bottom:0;height:3px;background:var(--blue)}

/* hero */
.hero{position:absolute;left:0;top:117px;width:1200px;height:565px;background:linear-gradient(110deg,#d4d2d0 0%,#b9b4ae 45%,#8d7f72 75%,#5c5148 100%)}
.hero-box{position:absolute;left:111px;top:152px;width:547px;height:265px;background:rgba(255,255,255,.72);padding:26px 17px}
.hero-box h1{font-size:39px;font-weight:700;color:var(--ink);letter-spacing:-.5px;line-height:1.1}
.hero-box h1 span{color:var(--blue)}
.hero-box p{margin-top:16px;font-size:16px;line-height:28px;color:#222}
.hero-arrow{position:absolute;top:265px;width:34px;height:34px;border-radius:50%;background:rgba(40,40,40,.7);display:flex;align-items:center;justify-content:center}

/* services */
.service{position:absolute;top:843px;width:311px;height:380px}
.service .photo{position:absolute;left:0;top:0;width:311px;height:224px}
.service .badge{position:absolute;right:0;top:156px;width:63px;height:50px;background:var(--blue);display:flex;align-items:center;justify-content:center}
.service .card{position:absolute;left:23px;top:206px;width:288px;height:174px;background:var(--white);box-shadow:0 3px 12px rgba(0,0,0,.1);padding:22px 28px}
.service h3{font-family:'Roboto',sans-serif;font-size:17px;font-weight:700;text-transform:uppercase}
.service p{margin-top:12px;font-size:13px;line-height:21px;color:var(--text)}
.read-more{display:flex;align-items:center;gap:7px;margin-top:14px;font-size:14px;font-weight:700;color:var(--blue)}

/* about */
.about{position:absolute;left:0;top:1327px;width:1200px;height:730px;background:var(--grey-bg)}
.about-frame{position:absolute;left:111px;top:73px;width:386px;height:558px;background:var(--blue)}
.about-photo{position:absolute;left:120px;top:82px;width:467px;height:541px;background:linear-gradient(160deg,#c9c8c4,#8f8e8a 60%,#6b6a67)}
.about-label{position:absolute;left:648px;top:118px;display:flex;align-items:center;gap:12px;color:var(--blue);font-weight:700;font-size:15px}
.about-label i{display:block;width:45px;height:2px;background:var(--blue);margin-top:8px}
.about h2{position:absolute;left:648px;top:145px;width:440px;font-size:24px;font-weight:600;line-height:33px}
.about-text{position:absolute;left:648px;top:232px;width:440px;font-size:14px;line-height:26px;color:var(--text)}
.about-text p+p{margin-top:14px}
.owned-badge{position:absolute;left:648px;top:520px;width:87px;height:87px;border-radius:50%;background:#2f8a3d;border:5px solid #e8e8e8;box-shadow:0 0 0 2px #2f8a3d}

/* features */
.features{position:absolute;left:0;top:2057px;width:1200px;height:466px;background:linear-gradient(90deg,#1f83c9,#1a8ad3 50%,#1680cb)}
.feature{position:absolute;top:0;width:320px;text-align:center;color:var(--white)}
.feature .ring{margin:55px auto 0;width:156px;height:156px;border-radius:50%;border:3px solid var(--white);display:flex;align-items:center;justify-content:center}
.feature .disc{width:136px;height:136px;border-radius:50%;background:var(--white);display:flex;align-items:center;justify-content:center}
.feature h3{margin-top:27px;font-family:'Roboto',sans-serif;font-size:18px;font-weight:700}
.feature p{margin:14px auto 0;width:270px;font-size:14px;line-height:20px}
.feature .btn{position:relative;margin:0 auto;width:158px;height:45px;background:var(--navy);font-size:14px}

/* projects */
.project{position:absolute;width:314px;height:214px}

/* customers */
.customers{position:absolute;left:0;top:3240px;width:1200px;height:307px;background:var(--sky-bg)}
.client{position:absolute;top:144px;width:166px;height:83px;background:var(--white);box-shadow:0 2px 8px rgba(0,0,0,.08);display:flex;align-items:center;justify-content:center;gap:8px;font-family:'Roboto',sans-serif;font-weight:500;font-size:16px;color:var(--ink)}
.client i{display:block;width:14px;height:14px;border-radius:50%;background:var(--muted-shape)}
.client .plain-badge{width:54px;height:54px;border-radius:50%;background:var(--muted-shape)}
.client .plain-square{width:46px;height:46px;border-radius:0;background:var(--muted-shape)}
.car-arrow{position:absolute;top:170px;width:32px;height:32px;border-radius:50%;background:var(--white);box-shadow:0 1px 6px rgba(0,0,0,.15);display:flex;align-items:center;justify-content:center}

/* contact */
.contact-item{position:absolute;top:3724px;display:flex;gap:16px}
.contact-item h4{font-size:15px;font-weight:700}
.contact-item p{font-size:14px;line-height:20px;color:var(--text)}
.get-touch{position:absolute;left:137px;top:3838px;font-family:'Roboto',sans-serif;font-size:24px;font-weight:700}
.reach{position:absolute;left:137px;top:3894px;font-size:15px;color:#444}
.field{position:absolute;left:137px;width:404px;height:41px;border:1px solid #e3e3e3;box-shadow:0 2px 5px rgba(0,0,0,.06);padding:12px 22px;font-size:12px;color:#555;background:var(--white)}
.submit{position:absolute;left:137px;top:4223px;width:404px;height:40px;background:var(--blue);color:var(--white);font-weight:700;font-size:15px;display:flex;align-items:center;justify-content:center}
.map{position:absolute;left:594px;top:3835px;width:428px;height:428px;background:linear-gradient(135deg,#eeeeee,#e2e3e5)}
.map-tag{position:absolute;left:108px;top:111px;width:180px;height:52px;background:var(--white);box-shadow:0 2px 8px rgba(0,0,0,.2);display:flex;align-items:center;justify-content:center;gap:6px;font-family:'Poppins',sans-serif;font-weight:700;font-size:13px;color:var(--blue)}
.map-tag i{display:block;width:14px;height:14px;border-radius:50%;background:var(--blue)}

/* footer */
.footer{position:absolute;left:0;top:4368px;width:1200px;height:251px;background:var(--footer);color:var(--white)}
.footer-nav{position:absolute;top:60px;left:0;width:1200px;text-align:center;font-size:15px}
.footer-nav span{margin:0 8px;color:#ccc}
.footer-line{position:absolute;left:111px;display:flex;gap:16px;align-items:center;font-size:14px}
.footer-social{position:absolute;left:469px;top:115px;display:flex;gap:13px}
.footer-social i{display:block;width:42px;height:42px;border-radius:50%;border:2px solid var(--white)}
.pay{position:absolute;left:517px;top:186px;display:flex;gap:4px}
.pay span{width:30px;height:18px;background:var(--blue);border-radius:2px}
.copy{position:absolute;right:113px;top:128px;text-align:right;font-size:14px;line-height:37px}
.footer-bar{position:absolute;left:0;bottom:0;width:1200px;height:4px;background:var(--blue)}
</style>
</head>
<body>

<header class="header">
  <div class="logo"><i class="logo-dot"></i><span class="logo-name">Call The Pipe Team</span></div>
  <div class="stay">Stay Connected :</div>
  <div class="social-top" style="left:776px"><i aria-label="social link"></i><i aria-label="social link"></i><i aria-label="social link"></i></div>
  <div class="estimate">
    <svg width="20" height="34" viewBox="0 0 20 34"><rect x="2" y="1" width="16" height="32" rx="3" fill="none" stroke="#1c1c1c" stroke-width="2.5"/><circle cx="10" cy="28" r="1.6" fill="#1c1c1c"/></svg>
    <div><small>Request A Free Estimate</small><b>1800 000 123</b></div>
  </div>
  <nav class="nav">
    <a class="active">Home</a><a>About Us</a><a>Services</a><a>Septics</a><a>Products</a><a>Clients</a><a>Contact Us</a>
  </nav>
</header>

<section class="hero" role="img" aria-label="Plumber fitting pipework beneath a basin">
  <div class="hero-box">
    <h1><span>Call The</span> Pipe Team</h1>
    <p>Call The Pipe Team is a family run business based in Northvale since 2004, we service Eastbrook to Westmere, Lakeford to</p>
  </div>
  <div class="btn" style="left:129px;top:326px;width:190px;height:52px;background:var(--blue)">Read More
    <svg viewBox="0 0 14 14"><circle cx="7" cy="7" r="7" fill="#fff"/><path d="M5.5 4l3 3-3 3" stroke="#1a86d0" stroke-width="1.8" fill="none"/></svg></div>
  <div class="hero-arrow" style="left:33px"><svg width="10" height="12"><path d="M8 1L2 6l6 5z" fill="#fff"/></svg></div>
  <div class="hero-arrow" style="left:1131px"><svg width="10" height="12"><path d="M2 1l6 5-6 5z" fill="#fff"/></svg></div>
</section>

<h2 class="section-title" style="top:774px">OUR <span>SERVICES</span></h2>

<div class="service" style="left:111px">
  <div class="photo" role="img" aria-label="Plumber working under a sink" style="background:linear-gradient(135deg,#4d86c4,#9fb8cc 55%,#d9dde0)"></div>
  <div class="badge"><svg width="30" height="30" viewBox="0 0 30 30" fill="none" stroke="#fff" stroke-width="2"><path d="M5 4v10h10v12"/><path d="M20 6h6v6"/></svg></div>
  <div class="card"><h3>Plumbing</h3><p>Set-up all pipework for new housing or renovations including compliance paperwork</p>
    <div class="read-more">READ MORE <svg width="13" height="13" viewBox="0 0 14 14"><circle cx="7" cy="7" r="7" fill="#1a86d0"/><path d="M5.5 4l3 3-3 3" stroke="#fff" stroke-width="1.8" fill="none"/></svg></div></div>
</div>
<div class="service" style="left:445px">
  <div class="photo" role="img" aria-label="Gas fitter at an industrial gas installation" style="background:linear-gradient(135deg,#c7b493,#a9a39a 50%,#e07a3a 75%,#8a8f96)"></div>
  <div class="badge"><svg width="30" height="30" viewBox="0 0 30 30" fill="none" stroke="#fff" stroke-width="2"><circle cx="15" cy="9" r="4"/><path d="M4 20h22M8 20v6M22 20v6M15 13v7"/></svg></div>
  <div class="card"><h3>Gas</h3><p>All gas pipework installations to kitchen, heaters, BBQ's and Hot water Units</p>
    <div class="read-more">READ MORE <svg width="13" height="13" viewBox="0 0 14 14"><circle cx="7" cy="7" r="7" fill="#1a86d0"/><path d="M5.5 4l3 3-3 3" stroke="#fff" stroke-width="1.8" fill="none"/></svg></div></div>
</div>
<div class="service" style="left:777px">
  <div class="photo" role="img" aria-label="Technician repairing wall-mounted pipes" style="background:linear-gradient(135deg,#b8b2a6,#8e8a83 50%,#c9c3b6)"></div>
  <div class="badge"><svg width="30" height="30" viewBox="0 0 30 30" fill="none" stroke="#fff" stroke-width="2"><path d="M6 24L20 10M18 6a5 5 0 0 0 6 6M6 6l18 18M4 8l4-4"/></svg></div>
  <div class="card"><h3>Repairs &amp; Maintenance</h3><p>Set-up all pipework for new housing or renovations including compliance paperwork</p>
    <div class="read-more">READ MORE <svg width="13" height="13" viewBox="0 0 14 14"><circle cx="7" cy="7" r="7" fill="#1a86d0"/><path d="M5.5 4l3 3-3 3" stroke="#fff" stroke-width="1.8" fill="none"/></svg></div></div>
</div>

<section class="about">
  <div class="about-frame"></div>
  <div class="about-photo" role="img" aria-label="Owner standing in a sink showroom"></div>
  <div class="about-label"><i></i>ABOUT CALL THE PIPE TEAM</div>
  <h2>We are an plumbing and gas Services Provider in Australia</h2>
  <div class="about-text">
    <p>Dan has been in the plumbing and gas industry since high school, his father Ray was a plumber and estimator. Dan has trained with reputable plumbers of his time and achieved apprentice of the year 2 years running, then taking out the “Apprentice of the Year” award for all trades during his apprenticeship.</p>
    <p>A member of Trade Plumbers Guild trade-plumbing and an Eco-West Plumber Eco-West Dan maintains a high level of education and frequently refreshes his knowledge with current trends and regulations.</p>
  </div>
  <div class="owned-badge" role="img" aria-label="Locally owned badge"></div>
  <div class="btn" style="left:777px;top:538px;width:154px;height:47px;background:var(--blue);font-size:14px">Read More
    <svg viewBox="0 0 14 14"><circle cx="7" cy="7" r="7" fill="#fff"/><path d="M5.5 4l3 3-3 3" stroke="#1a86d0" stroke-width="1.8" fill="none"/></svg></div>
</section>

<section class="features">
  <div class="feature" style="left:84px">
    <div class="ring"><div class="disc"><svg width="80" height="80" viewBox="0 0 80 80" fill="none" stroke="#1a86d0" stroke-width="2.5"><rect x="10" y="12" width="38" height="44" rx="3"/><path d="M18 26l6 6 14-14"/><circle cx="52" cy="52" r="16"/><path d="M52 42v10l7 5M48 32h8"/></svg></div></div>
    <h3>QUICK RESPONSE</h3>
    <p>If you've had enough of tradespeople who never turn up when they say they will, call Dan at Call The Pipe Team.</p>
    <div class="btn" style="margin-top:34px">Read More <svg viewBox="0 0 14 14"><circle cx="7" cy="7" r="7" fill="#fff"/><path d="M5.5 4l3 3-3 3" stroke="#0f1a4f" stroke-width="1.8" fill="none"/></svg></div>
  </div>
  <div class="feature" style="left:437px">
    <div class="ring"><div class="disc"><svg width="80" height="80" viewBox="0 0 80 80" fill="none" stroke="#1a86d0" stroke-width="2.5"><rect x="22" y="8" width="36" height="64" rx="5"/><circle cx="42" cy="38" r="13"/><path d="M42 30v16M46 33h-6a3 3 0 0 0 0 6h4a3 3 0 0 1 0 6h-6"/><path d="M8 30h12M8 40h12M8 50h12"/></svg></div></div>
    <h3>PAYMENT OPTIONS</h3>
    <p>Electronic Transfer, CardOne and CardTwo accepted, Debit Cards and EFTPOS facilities, Credit account to approved clients only,</p>
    <div class="btn" style="margin-top:14px">Read More <svg viewBox="0 0 14 14"><circle cx="7" cy="7" r="7" fill="#fff"/><path d="M5.5 4l3 3-3 3" stroke="#0f1a4f" stroke-width="1.8" fill="none"/></svg></div>
  </div>
  <div class="feature" style="left:791px">
    <div class="ring"><div class="disc"><svg width="80" height="80" viewBox="0 0 80 80" fill="none" stroke="#1a86d0" stroke-width="2.5"><path d="M10 38h60v6a26 26 0 0 1-52 0"/><path d="M32 70h16M40 62v8"/><path d="M40 38V18a6 6 0 0 1 12 0v4"/></svg></div></div>
    <h3>VIEW OUR SHOWROOM</h3>
    <p>We handle all plumbing and gas installation including domestic and commercial.</p>
    <div class="btn" style="margin-top:34px">Read More <svg viewBox="0 0 14 14"><circle cx="7" cy="7" r="7" fill="#fff"/><path d="M5.5 4l3 3-3 3" stroke="#0f1a4f" stroke-width="1.8" fill="none"/></svg></div>
  </div>
</section>

<h2 class="section-title" style="top:2618px">LATEST <span>PROJECTS</span></h2>
<div class="project" style="left:111px;top:2690px;background:linear-gradient(135deg,#b9b6b2,#7a7f86)" role="img" aria-label="Plumber fixing a basin waste"></div>
<div class="project" style="left:443px;top:2690px;background:linear-gradient(135deg,#e6e6e6,#4f74ae 55%,#c98aa6)" role="img" aria-label="Plumber laying heating pipes beside a radiator"></div>
<div class="project" style="left:773px;top:2690px;background:linear-gradient(135deg,#d3d3d3,#5a5a5a 55%,#c9c9c9)" role="img" aria-label="Wrench on sink trap pipework"></div>
<div class="project" style="left:111px;top:2921px;background:linear-gradient(135deg,#d9d6cf,#8e95a6 55%,#c9c4ba)" role="img" aria-label="Owner in the bathroom showroom"></div>
<div class="project" style="left:443px;top:2921px;background:linear-gradient(135deg,#8a5b3d,#3c4c6a 55%,#2b2b2b)" role="img" aria-label="Technician servicing a hot water system"></div>
<div class="project" style="left:773px;top:2921px;background:linear-gradient(135deg,#a8b8c6,#2c5fb0 50%,#d8d8d8)" role="img" aria-label="Team installing a gas cooktop"></div>

<section class="customers">
  <h2 class="section-title" style="top:61px">CURRENT <span>CUSTOMERS</span></h2>
  <div class="car-arrow" style="left:41px"><svg width="8" height="10"><path d="M7 0L1 5l6 5z" fill="#1c1c1c"/></svg></div>
  <div class="client" style="left:118px"><i></i>Brightfield</div>
  <div class="client" style="left:316px"><i></i>Warmline</div>
  <div class="client" style="left:515px"><i></i>Keystone Pumps</div>
  <div class="client" style="left:714px" role="img" aria-label="Industry association badge"><i class="plain-badge"></i></div>
  <div class="client" style="left:913px" role="img" aria-label="Industry certification badge"><i class="plain-square"></i></div>
  <div class="car-arrow" style="left:1123px"><svg width="8" height="10"><path d="M1 0l6 5-6 5z" fill="#1c1c1c"/></svg></div>
</section>

<h2 class="section-title" style="top:3654px">CONTACT <span>US</span></h2>
<div class="contact-item" style="left:160px">
  <svg width="50" height="56" viewBox="0 0 50 56" fill="none" stroke="#1a86d0" stroke-width="2.2"><path d="M25 44S11 30 11 19a14 14 0 0 1 28 0c0 11-14 25-14 25z"/><circle cx="25" cy="19" r="5"/><path d="M14 40L4 52h42L36 40"/></svg>
  <div><h4>LOCATION:</h4><p>27 Ridgeway Street Northvale<br>WA 6500</p></div>
</div>
<div class="contact-item" style="left:470px">
  <svg width="58" height="50" viewBox="0 0 58 50" fill="none" stroke="#1a86d0" stroke-width="2.2"><path d="M4 20L29 4l25 16v26H4z"/><path d="M4 20l25 16 25-16M4 46l18-16M54 46L36 30"/></svg>
  <div style="padding-top:8px"><h4>EMAIL:</h4><p>office@callthepipeteam.com.au</p></div>
</div>
<div class="contact-item" style="left:843px">
  <svg width="50" height="50" viewBox="0 0 50 50" fill="none" stroke="#1a86d0" stroke-width="2.2"><path d="M10 6l8 9-4 5c3 7 8 12 15 15l5-4 9 8-6 6C20 44 6 30 5 12z"/><path d="M28 8a14 14 0 0 1 14 14M28 2a20 20 0 0 1 20 20"/></svg>
  <div><h4>PHONE:</h4><p>(08) 9000 0144<br>0400 000 789</p></div>
</div>

<h3 class="get-touch">GET IN TOUCH</h3>
<p class="reach">Reach out to us for any inquiry</p>
<div class="field" style="top:3940px">First Name</div>
<div class="field" style="top:3995px">Last Name</div>
<div class="field" style="top:4050px">Phone Number</div>
<div class="field" style="top:4106px;height:83px">Message</div>
<div class="submit">SUBMIT</div>

<div class="map" role="img" aria-label="Street map showing the business location">
  <div class="map-tag"><i></i>Call The Pipe Team</div>
  <svg class="abs" style="left:182px;top:190px" width="30" height="40" viewBox="0 0 30 40"><path d="M15 38S3 22 3 14a12 12 0 0 1 24 0c0 8-12 24-12 24z" fill="#1a86d0"/><circle cx="15" cy="14" r="4.5" fill="#fff"/></svg>
</div>

<footer class="footer">
  <div class="footer-nav">Home<span>|</span>Company<span>|</span>Services<span>|</span>Products<span>|</span>Contact Us<span>|</span>Terms &amp; Conditions<span>|</span>FAQs</div>
  <div class="footer-line" style="top:126px">
    <svg width="18" height="18" viewBox="0 0 18 18" fill="none" stroke="#aaa" stroke-width="1.4"><path d="M3 2l3 3-1.5 2c1 2.5 3 4.5 5.5 5.5L12 11l3 3-2 2C7 15 3 11 2 4z"/></svg>1800 000 123</div>
  <div class="footer-line" style="top:168px">
    <svg width="18" height="14" viewBox="0 0 18 14" fill="none" stroke="#aaa" stroke-width="1.4"><rect x="1" y="1" width="16" height="12"/><path d="M1 1l8 7 8-7"/></svg>office@callthepipeteam.com.au</div>
  <div class="footer-social" aria-label="social links"><i></i><i></i><i></i><i></i><i></i></div>
  <div class="pay" aria-label="accepted payment methods"><span></span><span></span><span></span><span></span><span></span></div>
  <div class="copy">© Copyright 2020 &nbsp;Call The Pipe Team.<br>All Rights Reserved</div>
  <div class="footer-bar"></div>
</footer>

</body>
</html>
```